Copperleaf Roofing Business Card

This is my current business card. But I’d like to make some changes. Somewhere on the card I’d like to list some of the services we offer. Maybe on the back? But I’d still like to keep the red. White and black modern look.

-residential & commercial roofing
-Roof Repairs & Maintenance
-Storm Damage & Insurance Claims specialist
-Christmas Lights and permanent Christmas lights
Fencing. Windows. Gutters. Siding. Sheetrock, painting.

```html
<!DOCTYPE html>
<html lang="en">
<head>
<meta charset="utf-8">
<title>Copperleaf Roofing Business Card</title>
<link href="https://fonts.googleapis.com/css2?family=Lato:wght@400;700;900&family=Michroma&display=swap" rel="stylesheet">
<style>
  :root {
    --stage: #3a3a3c;
    --ink: #0a0a0a;
    --paper: #ffffff;
    --red: #e3141b;
    --text-dark: #1a1a1a;
    --text-light: #f4f4f4;
  }
  * { box-sizing: border-box; margin: 0; padding: 0; }
  html, body { width: 1200px; height: 694px; overflow: hidden; }
  body {
    background: var(--stage);
    font-family: "Lato", sans-serif;
    display: flex;
    align-items: center;
    justify-content: center;
    gap: 40px;
  }
  .card {
    width: 560px;
    height: 320px;
    border-radius: 22px;
    position: relative;
    overflow: hidden;
    box-shadow: 0 18px 40px rgba(0,0,0,.45);
  }

  /* Back side */
  .card-back { background: var(--ink); color: var(--text-light); }
  .card-back .brand {
    position: absolute; left: 34px; top: 90px; width: 200px;
    display: flex; flex-direction: column; align-items: center; gap: 14px;
  }
  .brand-dot {
    width: 92px; height: 92px; border-radius: 50%;
    background: var(--red); border: 3px solid var(--paper);
  }
  .brand-name {
    font-family: "Lato", sans-serif; font-weight: 900;
    font-size: 24px; line-height: 1.05; text-align: center;
    text-transform: uppercase; letter-spacing: 1px;
    color: var(--red);
  }
  .divider {
    position: absolute; left: 258px; top: 40px; width: 2px; height: 240px;
    background: linear-gradient(to bottom, transparent, var(--red) 30%, var(--red) 70%, transparent);
  }
  .services {
    position: absolute; left: 284px; top: 50px; right: 24px;
    list-style: none; font-size: 15.5px; line-height: 1.4;
  }
  .services li { position: relative; padding-left: 16px; }
  .services li::before {
    content: ""; position: absolute; left: 0; top: 8px;
    width: 6px; height: 6px; border-radius: 50%; background: var(--red);
  }
  .services li.plain::before { display: none; }

  /* Front side */
  .card-front { background: var(--paper); color: var(--text-dark); }
  .card-front .brand {
    position: absolute; right: 40px; top: 36px;
    display: flex; flex-direction: column; align-items: center; gap: 10px;
  }
  .card-front .brand-dot { width: 80px; height: 80px; border-color: var(--paper); }
  .card-front .brand-name { font-size: 22px; }
  .rule {
    position: absolute; left: 40px; right: 40px; top: 190px;
    height: 1.5px; background: var(--text-dark);
  }
  .person { position: absolute; left: 40px; top: 128px; }
  .person-name {
    font-family: "Michroma", sans-serif; font-size: 24px;
    color: var(--red); text-transform: uppercase; letter-spacing: 1px;
  }
  .person-role { font-size: 15px; margin-top: 4px; }
  .contacts {
    position: absolute; left: 40px; top: 206px;
    list-style: none; font-size: 14.5px; line-height: 1.55;
  }
  .contacts li { display: flex; align-items: center; gap: 10px; }
  .contacts svg { width: 14px; height: 14px; fill: var(--red); flex: none; }
  .address {
    position: absolute; right: 40px; top: 206px;
    font-size: 14.5px; line-height: 1.55; text-align: right;
  }
</style>
</head>
<body>

  <section class="card card-back" aria-label="Card back">
    <div class="brand">
      <span class="brand-dot" aria-hidden="true"></span>
      <span class="brand-name">Copperleaf<br>Roofing Co.</span>
    </div>
    <span class="divider" aria-hidden="true"></span>
    <ul class="services">
      <li>Residential &amp; commercial roofing</li>
      <li>Roof Repairs &amp; Maintenance</li>
      <li>Storm Damage &amp; Insurance<br>Claims specialist</li>
      <li>Christmas Lights and<br>permanent Christmas lights</li>
      <li>Fencing. Windows. Gutters.<br>Siding. Sheetrock, painting.</li>
    </ul>
  </section>

  <section class="card card-front" aria-label="Card front">
    <div class="brand">
      <span class="brand-dot" aria-hidden="true"></span>
      <span class="brand-name">Copperleaf<br>Roofing Co.</span>
    </div>

    <div class="person">
      <p class="person-name">Reid Calloway</p>
      <p class="person-role">Owner</p>
    </div>

    <span class="rule" aria-hidden="true"></span>

    <ul class="contacts">
      <li>
        <svg viewBox="0 0 24 24" aria-hidden="true"><path d="M6.6 10.8a15.1 15.1 0 0 0 6.6 6.6l2.2-2.2c.3-.3.7-.4 1-.2 1.1.4 2.3.6 3.6.6.6 0 1 .4 1 1V20c0 .6-.4 1-1 1C10.6 21 3 13.4 3 4c0-.6.4-1 1-1h3.5c.6 0 1 .4 1 1 0 1.3.2 2.5.6 3.6.1.3 0 .7-.2 1z"/></svg>
        555-014-2287
      </li>
      <li>
        <svg viewBox="0 0 24 24" aria-hidden="true"><path d="M2 5h20v14H2zm2 2v.5l8 5 8-5V7l-8 5z"/></svg>
        reid@copperleafroofing.co
      </li>
      <li>
        <svg viewBox="0 0 24 24" aria-hidden="true"><circle cx="12" cy="12" r="10"/></svg>
        www.copperleafroofing.co
      </li>
    </ul>

    <p class="address">421, Address line goes here<br>45452, Country name</p>
  </section>

</body>
</html>
```